Redesign for a start up airline technology. The website is quelbrion.com.

I need a PowerPoint template that complements our website. I can provide our current template as a starting point.

```html
<!DOCTYPE html>
<html lang="en">
<head>
<meta charset="utf-8">
<title>Quelbrion Presentation Template</title>
<link href="https://fonts.googleapis.com/css2?family=Lexend:wght@300;400;500;600;700&family=Poppins:wght@400;500;600;700&display=swap" rel="stylesheet">
<style>
:root{
  --canvas:#4a4a4a;
  --white:#ffffff;
  --ink:#1b1b1b;
  --muted:#555;
  --blue:#0a3f8a;
  --blue-mid:#0b63b0;
  --sky:#1aa0d8;
  --green:#6cbf3a;
}
*{margin:0;padding:0;box-sizing:border-box}
html,body{width:1044px;height:1200px;overflow:hidden;background:var(--canvas)}
body{position:relative;font-family:"Lexend",sans-serif;color:var(--ink)}
.slide{position:absolute;width:485px;height:273px;background:var(--white);overflow:hidden}
.s1{left:23px;top:21px}.s2{left:536px;top:21px}
.s3{left:23px;top:316px}.s4{left:536px;top:316px}
.s5{left:23px;top:611px}.s6{left:536px;top:611px}
.s7{left:23px;top:906px}.s8{left:536px;top:906px}
.abs{position:absolute}
.brand-mini{position:absolute;right:10px;top:11px;font:700 10px "Lexend",sans-serif;color:var(--blue);letter-spacing:.2px}
.title{position:absolute;left:0;width:100%;text-align:center;font-weight:400}

.hero-photo{position:absolute;inset:0;background:linear-gradient(180deg,#eef1f3 0%,#f4f5f6 55%,#e6e9ec 100%)}
.brand-hero{position:absolute;left:0;width:100%;top:62px;text-align:center;font:700 40px "Lexend",sans-serif;color:var(--blue);letter-spacing:.5px}
.hero-head{top:133px;font-size:17px;line-height:23px;color:var(--ink)}
.pill{position:absolute;left:175px;top:190px;width:134px;height:22px;border-radius:11px;background:var(--green);color:var(--white);font-size:9.5px;line-height:22px;text-align:center;box-shadow:0 2px 5px rgba(0,0,0,.15)}
.year{top:223px;font-size:12px}

.sub{font-family:"Poppins",sans-serif;font-size:5.8px;line-height:10px;color:var(--ink)}
.svc-card{position:absolute;top:135px;width:89px;height:65px;background:var(--white);box-shadow:0 1px 6px rgba(0,0,0,.10)}
.svc-icon{position:absolute;top:-11px;left:34px;width:22px;height:22px;border-radius:50%;display:flex;align-items:center;justify-content:center}
.svc-list{position:absolute;left:11px;top:21px;list-style:none;font-family:"Poppins",sans-serif;font-size:4.4px;line-height:9px;color:var(--ink)}
.svc-list li{position:relative;padding-left:6px}
.svc-list li::before{content:"";position:absolute;left:0;top:2.6px;width:3.5px;height:3.5px;border-radius:50%;background:var(--dot)}

.about-photo{position:absolute;left:25px;top:27px;width:199px;height:217px;border-radius:7px;background:linear-gradient(160deg,#b9c6d6 0%,#d7b8c0 35%,#8d96a3 65%,#4c525a 100%)}
.about-h{left:239px;top:60px;font-size:15px}
.about-p{position:absolute;left:239px;width:218px;font-family:"Poppins",sans-serif;font-size:4.6px;line-height:10.2px;color:var(--ink)}

.globe{position:absolute;left:0;top:0;width:230px;height:273px;background:radial-gradient(circle at 55% 45%,#1d6f99 0%,#0e3b5c 45%,#071a2c 100%)}
.strut-h{left:261px;top:66px;font-size:16px;line-height:19px}
.tick-list{position:absolute;left:263px;top:118px;list-style:none;font-size:9px;font-weight:500;line-height:14px}
.tick-list li{position:relative;padding-left:11px;margin-bottom:8px}
.tick-list svg{position:absolute;left:0;top:3px}

.band{position:absolute;left:0;top:75px;width:100%;height:128px;background:linear-gradient(100deg,#0a4d8f 0%,#0b5ea6 50%,#179ad3 100%)}
.band-h{top:91px;font-size:15px;color:var(--white);font-weight:500}
.band-lead{top:122px;font-size:7.8px;color:var(--white);font-weight:300}
.band-body{top:138px;font-size:8.4px;line-height:14.6px;color:var(--white);font-weight:500}

.team-h{top:28px;font-size:16px}
.member{position:absolute;top:97px;width:100px;height:135px;background:var(--white);box-shadow:0 1px 6px rgba(0,0,0,.10);text-align:center}
.portrait{position:absolute;left:12px;top:-29px;width:76px;height:76px;border-radius:50%;background:linear-gradient(180deg,#d9d9d9 0%,#b9b2ab 100%)}
.m-name{position:absolute;top:56px;width:100%;font-size:8px;font-weight:500}
.m-role{position:absolute;top:67px;width:100%;font-family:"Poppins",sans-serif;font-size:5.2px;color:#999}
.m-bio{position:absolute;top:79px;left:4px;right:4px;font-family:"Poppins",sans-serif;font-size:5.7px;line-height:9.7px;color:#333}

.chart-h{top:40px;font-size:16px}
.stat{position:absolute;left:34px;font-weight:600;font-size:22px;line-height:22px}
.stat-l{position:absolute;left:34px;font-size:6px;font-weight:500}
.blue{color:var(--blue)}.green{color:var(--green)}
.col-h{position:absolute;left:350px;font-size:11px;font-weight:600}
.col-p{position:absolute;left:350px;width:105px;font-family:"Poppins",sans-serif;font-size:4px;line-height:7.5px;color:#333}

.brand-end{position:absolute;left:0;width:100%;top:60px;text-align:center;font:700 42px "Lexend",sans-serif;color:var(--blue)}
.thanks{top:137px;font-size:21px;font-weight:500}
.contact{position:absolute;top:180px;display:flex;align-items:center;gap:6px;font-size:6.6px;line-height:9px}
.c-icon{width:19px;height:19px;border-radius:50%;display:flex;align-items:center;justify-content:center;flex:none}
.c-strong{font-weight:600;font-size:7.6px}
</style>
</head>
<body>

<section class="slide s1">
  <div class="hero-photo" role="img" aria-label="Soft, hazy photograph of airliners on an airport apron"></div>
  <div class="brand-hero">Quelbrion</div>
  <h1 class="title hero-head">Unlocking the Future of Airline Operations<br>and the Flying Experience</h1>
  <div class="pill">www.quelbrion.com</div>
  <p class="title year">2024</p>
</section>

<section class="slide s2">
  <div class="brand-mini">Quelbrion</div>
  <h2 class="title" style="top:40px;font-size:17px">Our Services</h2>
  <p class="title sub" style="top:65px">Lorem ipsum dolor sit amet, consectetur adipiscing elit, sed do eiusmod tempor incididunt<br>ut labore et dolore magna aliqua.</p>

  <div class="svc-card" style="left:38px;--dot:var(--blue)">
    <div class="svc-icon" style="background:var(--blue)"><svg width="11" height="11" viewBox="0 0 24 24"><circle cx="12" cy="12" r="7" fill="none" stroke="#fff" stroke-width="4" stroke-dasharray="3.5 2"/><circle cx="12" cy="12" r="3" fill="#fff"/></svg></div>
    <ul class="svc-list"><li>Lorem ipsum dolor sit amet,</li><li>Lorem ipsum dolor sit amet,</li><li>Lorem ipsum dolor sit amet,</li><li>Lorem ipsum dolor sit amet,</li></ul>
  </div>
  <div class="svc-card" style="left:142px;--dot:var(--green)">
    <div class="svc-icon" style="background:var(--green)"><svg width="10" height="10" viewBox="0 0 24 24"><rect x="5" y="3" width="14" height="18" rx="2" fill="none" stroke="#fff" stroke-width="2.5"/><path d="M9 9h6M9 13h6M9 17h4" stroke="#fff" stroke-width="2"/></svg></div>
    <ul class="svc-list"><li>Lorem ipsum dolor sit amet,</li><li>Lorem ipsum dolor sit amet,</li><li>Lorem ipsum dolor sit amet,</li><li>Lorem ipsum dolor sit amet,</li></ul>
  </div>
  <div class="svc-card" style="left:244px;--dot:var(--blue)">
    <div class="svc-icon" style="background:var(--blue)"><svg width="10" height="10" viewBox="0 0 24 24"><circle cx="10" cy="10" r="6" fill="none" stroke="#fff" stroke-width="2.5"/><path d="M15 15l6 6" stroke="#fff" stroke-width="3"/></svg></div>
    <ul class="svc-list"><li>Lorem ipsum dolor sit amet,</li><li>Lorem ipsum dolor sit amet,</li><li>Lorem ipsum dolor sit amet,</li><li>Lorem ipsum dolor sit amet,</li></ul>
  </div>
  <div class="svc-card" style="left:347px;--dot:var(--green)">
    <div class="svc-icon" style="background:var(--green)"><svg width="10" height="10" viewBox="0 0 24 24"><path d="M3 4h18v12H9l-5 4V4z" fill="none" stroke="#fff" stroke-width="2.5"/><path d="M7 9h10M7 12h7" stroke="#fff" stroke-width="2"/></svg></div>
    <ul class="svc-list"><li>Lorem ipsum dolor sit amet,</li><li>Lorem ipsum dolor sit amet,</li><li>Lorem ipsum dolor sit amet,</li><li>Lorem ipsum dolor sit amet,</li></ul>
  </div>
</section>

<section class="slide s3">
  <div class="brand-mini">Quelbrion</div>
  <div class="about-photo" role="img" aria-label="Photograph of a jet airliner taking off from a runway at sunset"></div>
  <h2 class="abs about-h" style="font-weight:400">About Us</h2>
  <p class="about-p" style="top:84px">Quelbrion is an aerospace technology company that produces a game changing on-board weight and balance measurement system – the Load Sense Measurement Array (LSMA). The LSMA hardware kit automatically calculates an aircraft's weight and center of gravity for each flight.</p>
  <p class="about-p" style="top:135px">With numerous design, process and method patents, Quelbrion brings a unique combination of engineering innovation and certification expertise within the airline and aerospace industries.</p>
  <p class="about-p" style="top:186px">The Quelbrion leadership team holds decades of airline and relevant aviation experience, including a FAA delegated authority in the areas of Electrical Systems and Certification Management as a Designated Engineering Representative (DER).</p>
</section>

<section class="slide s4">
  <div class="globe" role="img" aria-label="Illustration of Earth at night with glowing network connections between cities"></div>
  <div class="brand-mini">Quelbrion</div>
  <h2 class="abs strut-h" style="font-weight:400">The Load Sense<br>Measurement Array</h2>
  <ul class="tick-list">
    <li><svg width="7" height="7" viewBox="0 0 10 10"><circle cx="5" cy="5" r="5" fill="#1aa0d8"/><path d="M2.6 5.2l1.6 1.6 3.2-3.4" stroke="#fff" stroke-width="1.3" fill="none"/></svg>An automated onboard weight<br>and balance measurement system</li>
    <li><svg width="7" height="7" viewBox="0 0 10 10"><circle cx="5" cy="5" r="5" fill="#1aa0d8"/><path d="M2.6 5.2l1.6 1.6 3.2-3.4" stroke="#fff" stroke-width="1.3" fill="none"/></svg>27 Patents (Awarded and Pending)</li>
    <li><svg width="7" height="7" viewBox="0 0 10 10"><circle cx="5" cy="5" r="5" fill="#1aa0d8"/><path d="M2.6 5.2l1.6 1.6 3.2-3.4" stroke="#fff" stroke-width="1.3" fill="none"/></svg>Over 3,000 Commercial Flights</li>
  </ul>
</section>

<section class="slide s5">
  <div class="brand-mini">Quelbrion</div>
  <div class="band" role="img" aria-label="Blue-toned photograph of a hand holding a small paper aircraft"></div>
  <h2 class="title band-h">Sustainability</h2>
  <p class="title band-lead">We are dedicated to helping our customers achieve zero carbon emissions by 2050.</p>
  <p class="title band-body">Our next-generation technology focuses on improving fuel burn efficiency to<br>significantly reduce CO2 emissions from aircraft, promote sustainability,<br>streamline operations, and contribute to a greener aviation industry.</p>
</section>

<section class="slide s6">
  <div class="brand-mini">Quelbrion</div>
  <h2 class="title team-h">Our Team</h2>
  <div class="member" style="left:34px"><div class="portrait" role="img" aria-label="Portrait photo of team member"></div><div class="m-name">Marten Vos</div><div class="m-role">Lorem Ipsum</div><p class="m-bio">Lorem ipsum dolor sit amet, consectetur adipiscing elit, sed do eiusmod tempor incid-idunt ut labore et dolore magna aliqua. Quis ipsum</p></div>
  <div class="member" style="left:140px"><div class="portrait" role="img" aria-label="Portrait photo of team member"></div><div class="m-name">Lina Vorst</div><div class="m-role">Lorem Ipsum</div><p class="m-bio">Lorem ipsum dolor sit amet, consectetur adipiscing elit, sed do eiusmod tempor incid-idunt ut labore et dolore magna aliqua. Quis ipsum</p></div>
  <div class="member" style="left:245px"><div class="portrait" role="img" aria-label="Portrait photo of team member"></div><div class="m-name">Ruben Hale</div><div class="m-role">Lorem Ipsum</div><p class="m-bio">Lorem ipsum dolor sit amet, consectetur adipiscing elit, sed do eiusmod tempor incid-idunt ut labore et dolore magna aliqua. Quis ipsum</p></div>
  <div class="member" style="left:351px"><div class="portrait" role="img" aria-label="Portrait photo of team member"></div><div class="m-name">Tomas Reijn</div><div class="m-role">Lorem Ipsum</div><p class="m-bio">Lorem ipsum dolor sit amet, consectetur adipiscing elit, sed do eiusmod tempor incid-idunt ut labore et dolore magna aliqua. Quis ipsum</p></div>
</section>

<section class="slide s7">
  <div class="brand-mini">Quelbrion</div>
  <h2 class="title chart-h">Quelbrion Charts</h2>
  <div class="stat blue" style="top:120px">579</div>
  <div class="stat-l blue" style="top:145px">Lorem Ipsum</div>
  <div class="stat green" style="top:175px">678</div>
  <div class="stat-l green" style="top:200px">Lorem Ipsum</div>
  <svg class="abs" style="left:0;top:0" width="485" height="273" viewBox="0 0 485 273" font-family="Poppins, sans-serif" font-size="4.4" font-weight="600" text-anchor="middle" fill="#222">
    <rect x="124" y="154" width="19" height="66" fill="#6cbf3a"/>
    <rect x="155" y="99" width="19" height="121" fill="#0a3f8a"/>
    <rect x="186" y="110" width="19" height="110" fill="#6cbf3a"/>
    <rect x="218" y="128" width="19" height="92" fill="#0a3f8a"/>
    <rect x="245" y="137" width="19" height="83" fill="#6cbf3a"/>
    <rect x="273" y="165" width="19" height="55" fill="#0a3f8a"/>
    <rect x="300" y="137" width="19" height="83" fill="#6cbf3a"/>
    <line x1="108" y1="220.5" x2="335" y2="220.5" stroke="#ccc" stroke-width=".6"/>
    <text x="133.5" y="231">2017</text><text x="164.5" y="231">2018</text><text x="195.5" y="231">2019</text>
    <text x="227.5" y="231">2020</text><text x="254.5" y="231">2021</text><text x="282.5" y="231">2022</text><text x="309.5" y="231">2023</text>
  </svg>
  <h3 class="col-h" style="top:91px">Lorem Ipsum</h3>
  <p class="col-p" style="top:109px">Lorem ipsum dolor sit amet, consectetur adipiscing elit, sed do eiusmod tempor incididunt ut labore et dolore magna aliqua. Quis ipsum suspendisse ultrices gravida. Risus commodo viverra maecenas accumsan lacus vel facilisis.</p>
  <h3 class="col-h" style="top:162px">Lorem Ipsum</h3>
  <p class="col-p" style="top:180px">Lorem ipsum dolor sit amet, consectetur adipiscing elit, sed do eiusmod tempor incididunt ut labore et dolore magna aliqua. Quis ipsum suspendisse ultrices gravida. Risus commodo viverra maecenas accumsan lacus vel facilisis.</p>
</section>

<section class="slide s8">
  <div class="brand-end">Quelbrion</div>
  <h2 class="title thanks">Thank You</h2>
  <div class="contact" style="left:64px">
    <span class="c-icon" style="background:var(--green)"><svg width="8" height="9" viewBox="0 0 24 24"><path d="M12 2a7 7 0 0 0-7 7c0 5 7 13 7 13s7-8 7-13a7 7 0 0 0-7-7z" fill="#fff"/><circle cx="12" cy="9" r="2.6" fill="#6cbf3a"/></svg></span>
    <span>12b Quelbrion Lorem ipsum<br>dolor sit amet</span>
  </div>
  <div class="contact" style="left:199px">
    <span class="c-icon" style="background:var(--blue)"><svg width="8" height="8" viewBox="0 0 24 24"><path d="M6.6 10.8a15 15 0 0 0 6.6 6.6l2.2-2.2a1 1 0 0 1 1-.25 11 11 0 0 0 3.6.6 1 1 0 0 1 1 1V20a1 1 0 0 1-1 1A17 17 0 0 1 3 4a1 1 0 0 1 1-1h3.5a1 1 0 0 1 1 1 11 11 0 0 0 .6 3.6 1 1 0 0 1-.25 1z" fill="#fff"/></svg></span>
    <span>Phone<br><span class="c-strong">+31 (0)20 555 0148</span></span>
  </div>
  <div class="contact" style="left:329px">
    <span class="c-icon" style="background:var(--green)"><svg width="8" height="7" viewBox="0 0 24 18"><rect x="1" y="1" width="22" height="16" rx="2" fill="#fff"/><path d="M2 2l10 8 10-8" stroke="#6cbf3a" stroke-width="2" fill="none"/></svg></span>
    <span>Email<br><span style="font-size:5.8px">HELLO@QUELBRION.COM</span></span>
  </div>
</section>

</body>
</html>
```